Business card design Needed for new logo / Construction business, home extensions and new builds

We need a business card design using our new logo files which i will attach to this project :)

We are a small construction business specialising in home extensions, new builds and property development. We are very ambitious and would appreciate professional and elegant designs for our new business card.

Very serious about using the services on MakerQuarry and recently acquired our new logo from here :)

Please get involved, i will feedback when i can as i am very busy but can respond daily, thanks

Target Market(s)

People that want to build onto their houses, new building developments or adding too their existing property

Industry/Entity Type

Construction

Contact Information for Business Card

Renwick Tolliver Construction, Lionel Ashby (Managing Director), Tel 07822254961, email - info@renwick-tolliver, www.renwick-tolliver.co.uk

Colors

Designer to choose colors to be used in the design.

Requirements
Must have
• I like a deep grey on the back please. A lot of you have provided black from and back, try mixing things up a little. The black looks cool 😎 Thanks

```html
<!DOCTYPE html>
<html lang="en">
<head>
<meta charset="utf-8">
<title>Renwick Tolliver Construction – Business Card</title>
<link href="https://fonts.googleapis.com/css2?family=Open+Sans:wght@400;600;700&display=swap" rel="stylesheet">
<style>
  :root {
    --canvas: #18181a;
    --card-front: #1e1e21;
    --card-back-light: #7a7b7d;
    --card-back-dark: #5f6062;
    --silver: #d9dadc;
    --silver-soft: #b9babd;
    --gold: #d9a326;
    --back-mark: #4e4f51;
    --rule: #8e8f92;
  }
  * { box-sizing: border-box; margin: 0; padding: 0; }
  html, body {
    width: 1200px; height: 780px; overflow: hidden;
    background: var(--canvas);
    font-family: "Open Sans", Arial, sans-serif;
  }
  .sheet {
    width: 1200px; height: 780px;
    display: flex; align-items: center; justify-content: center; gap: 40px;
  }
  .card {
    position: relative;
    width: 540px; height: 309px;
    border-radius: 3px;
    box-shadow: 0 10px 30px rgba(0,0,0,.45);
    overflow: hidden;
  }
  /* Front */
  .card-front { background: var(--card-front); }
  .front-brand {
    position: absolute; left: 34px; top: 70px; width: 220px;
    display: flex; flex-direction: column; align-items: center; gap: 12px;
    text-align: center;
  }
  .brand-square { width: 16px; height: 16px; background: var(--gold); }
  .brand-name {
    font-size: 19px; font-weight: 600; line-height: 1.3;
    color: var(--silver); letter-spacing: .08em; text-transform: uppercase;
  }
  .divider { position: absolute; inset: 0; pointer-events: none; }
  .contact {
    position: absolute; left: 300px; top: 78px; right: 20px;
    color: var(--silver);
  }
  .person-name { font-size: 25px; font-weight: 700; line-height: 1.1; letter-spacing: .01em; }
  .person-name .surname { color: var(--gold); }
  .person-role { font-size: 12.5px; margin-top: 4px; color: var(--silver-soft); }
  .address { font-size: 12.5px; line-height: 1.45; margin-top: 10px; }
  .contact-list { list-style: none; margin-top: 10px; font-size: 12.5px; line-height: 1.6; }
  .contact-list li { display: flex; align-items: center; gap: 8px; }
  .contact-icon { width: 12px; height: 12px; flex: none; }
  /* Back */
  .card-back {
    background: linear-gradient(160deg, var(--card-back-light) 0%, var(--card-back-dark) 100%);
    display: flex; align-items: center; justify-content: center;
  }
  .back-brand { display: flex; flex-direction: column; align-items: center; gap: 14px; }
  .back-brand .brand-square { background: var(--back-mark); width: 20px; height: 20px; }
  .back-brand .brand-name { color: var(--back-mark); font-size: 24px; }
</style>
</head>
<body>
<main class="sheet">
  <section class="card card-front" aria-label="Business card front">
    <div class="front-brand">
      <span class="brand-square" aria-hidden="true"></span>
      <span class="brand-name">Renwick Tolliver<br>Construction</span>
    </div>
    <svg class="divider" width="540" height="309" viewBox="0 0 540 309" aria-hidden="true">
      <defs>
        <linearGradient id="ruleFade" x1="0" y1="0" x2="0" y2="1">
          <stop offset="0" stop-color="#8e8f92" stop-opacity="0.9"/>
          <stop offset="1" stop-color="#8e8f92" stop-opacity="0.2"/>
        </linearGradient>
      </defs>
      <line x1="290" y1="40" x2="270" y2="270" stroke="url(#ruleFade)" stroke-width="1"/>
    </svg>
    <div class="contact">
      <p class="person-name">Lionel <span class="surname">Ashby</span></p>
      <p class="person-role">Managing Director</p>
      <p class="address">Halden Road, Westmere<br>Ashcombe, AS4 2LP</p>
      <ul class="contact-list">
        <li>
          <svg class="contact-icon" viewBox="0 0 12 12" aria-hidden="true"><path fill="#d9a326" d="M2.4 1 4.2 3 3.3 4.2c.7 1.6 1.9 2.8 3.5 3.5L8 6.8l2 1.8-.9 1.9C5.6 10.4 1.6 6.4 1.5 2.9z"/></svg>
          0782 225 4961
        </li>
        <li>
          <svg class="contact-icon" viewBox="0 0 12 12" aria-hidden="true"><rect x="1" y="2.5" width="10" height="7" rx="1" fill="#d9a326"/><path d="M1.5 3 6 6.6 10.5 3" fill="none" stroke="#1e1e21" stroke-width="1"/></svg>
          info@renwick-tolliver.co.uk
        </li>
        <li>
          <svg class="contact-icon" viewBox="0 0 12 12" aria-hidden="true"><circle cx="6" cy="6" r="5" fill="none" stroke="#d9a326" stroke-width="1.2"/><ellipse cx="6" cy="6" rx="2" ry="5" fill="none" stroke="#d9a326" stroke-width="1"/><line x1="1" y1="6" x2="11" y2="6" stroke="#d9a326" stroke-width="1"/></svg>
          www.renwick-tolliver.co.uk
        </li>
      </ul>
    </div>
  </section>

  <section class="card card-back" aria-label="Business card back">
    <div class="back-brand">
      <span class="brand-square" aria-hidden="true"></span>
      <span class="brand-name">Renwick Tolliver<br>Construction</span>
    </div>
  </section>
</main>
</body>
</html>
```